New website for salon services and wedding hair and makeup

I am a professional hairstylist and makeup artist in Charleston, SC. I have my own company where I see clients for cut and color and I also go on site for weddings. I have a current website that I would like to update and change the style. I would like to add a contact form, map, additional pages and be mobile friendly. It is important to me that it have a site map and can show up in searches. I will need to add photos to the site every so often and would like to continue to work with the designer. I have a logo that I am happy with and have attached the file however if you think a new logo would help the look of the site I am open to it. My current website is www.brightcombstudio-example.com, I would like to change the style and layout so it looks up to date. Here are some links to sites that I like the look of but I don't want to limit your creativity. http://willowlanefolio-example.com/ http://www.runwaylensworks-example.com http://miraventhol-example.com/. I have attached a few files for mock up purposes, please let me know if you would like more content. Thank you!

Target Market(s)

Women, Brides

Industry/Entity Type

Hair And Beauty

Number of Pages Required

1 page

Font styles to use
Sans Serif
Script

Requirements
Must have
• Contact form, Mobile friendly, sitemap
Nice to have
• I really like the look for the sites I have included on the project description guide.
Should not have
• Nothing overly girly.

```html
<!DOCTYPE html>
<html lang="en">
<head>
<meta charset="utf-8">
<title>Brightcomb Hair &amp; Makeup</title>
<link rel="stylesheet" href="https://fonts.googleapis.com/css2?family=Josefin+Sans:wght@300;400;600&family=Pinyon+Script&display=swap">
<style>
:root{
  --ink:#2c3e50;
  --navy:#163d5c;
  --blue:#2a7ab8;
  --sky:#bfe3f2;
  --mint:#d6efd2;
  --grass:#8cc63f;
  --line:#8a8a8a;
  --muted:#555;
  --field:#ffffff;
  --btn:#1d4f74;
}
*{box-sizing:border-box;margin:0;padding:0}
html,body{width:1200px;height:2736px;overflow:hidden}
body{position:relative;font-family:"Josefin Sans",sans-serif;color:var(--ink);
  background:
   radial-gradient(ellipse 520px 420px at 300px 1250px,rgba(191,227,242,.55),transparent 70%),
   radial-gradient(ellipse 560px 460px at 900px 1180px,rgba(214,239,210,.6),transparent 70%),
   radial-gradient(ellipse 620px 500px at 620px 880px,rgba(191,227,242,.6),transparent 70%),
   radial-gradient(ellipse 500px 400px at 200px 1900px,rgba(214,239,210,.55),transparent 70%),
   radial-gradient(ellipse 520px 420px at 1000px 2000px,rgba(191,227,242,.45),transparent 70%),
   #fff}
.abs{position:absolute}
/* nav */
.site-nav{left:80px;top:56px;width:1040px;height:50px;border-bottom:2px solid #cfd8de}
.site-nav a{position:absolute;top:8px;font-size:30px;color:var(--ink);text-decoration:none}
.site-nav a.active{color:var(--blue);border-bottom:3px solid var(--blue)}
.nav-brand{position:absolute;left:430px;top:-6px;font-family:"Pinyon Script",cursive;font-size:42px;color:var(--blue)}
.page-tag{left:170px;top:14px;font-size:16px;color:var(--muted)}
/* hero */
.hero{left:40px;top:152px;width:1120px;height:560px;
  background:linear-gradient(100deg,#f4e6dc 0%,#8a4a2c 30%,#e8d6c8 55%,#d7cabd 70%,#3a2a22 100%)}
.hero-arrow{top:400px;width:36px;height:36px;border-radius:50%;background:rgba(255,255,255,.8)}
/* brand */
.brand{left:0;width:1200px;top:750px;text-align:center}
.brand-name{font-family:"Pinyon Script",cursive;font-size:120px;color:var(--navy);line-height:1}
.brand-sub{font-weight:300;font-size:52px;color:var(--navy);margin-top:6px;letter-spacing:1px}
/* section heads */
.section-head{left:80px;width:1040px;text-align:center;font-family:"Pinyon Script",cursive;font-size:60px;color:var(--navy)}
.section-head::before,.section-head::after{content:"";position:absolute;top:50%;width:360px;border-top:2px solid var(--line)}
.section-head::before{left:0}.section-head::after{right:0}
/* services */
.service{width:240px;text-align:center;top:1048px}
.service .photo{width:210px;height:250px;margin:0 auto;border-radius:50% 50% 46% 46%}
.service p{font-size:26px;margin-top:14px;color:var(--navy)}
/* works */
.works{left:80px;top:1448px;width:1040px;height:208px;display:flex;gap:12px}
.works div{flex:1}
/* timeline */
.timeline{left:60px;top:1700px;width:1080px}
.years{position:relative;height:30px;font-size:20px;color:var(--muted)}
.years span{position:absolute}
.events{position:relative;font-size:18px;color:var(--navy);line-height:1.2}
.events span{position:absolute;width:110px}
/* contact */
.contact-lead{left:40px;top:2110px;font-family:"Pinyon Script",cursive;font-size:44px;color:var(--navy)}
.contact-intro{left:290px;top:2200px;width:380px;font-family:"Pinyon Script",cursive;font-size:30px;line-height:1.25;color:var(--ink)}
.contact-line{left:300px;font-size:40px;color:var(--navy);display:flex;align-items:center;gap:22px;white-space:nowrap}
.contact-line.small{font-size:18px}
.thanks{left:290px;top:2520px;font-family:"Pinyon Script",cursive;font-size:30px;line-height:1.2;width:300px}
.person{left:20px;top:2220px;width:200px;height:420px;border-radius:90px 90px 20px 20px;
  background:linear-gradient(180deg,#e9d9b8,#fafafa 45%,#d9d9d9)}
.form-title{left:740px;top:2116px;font-family:"Pinyon Script",cursive;font-size:44px;color:var(--navy)}
.contact-form{left:740px;top:2192px;width:366px}
.field{display:block;width:100%;height:34px;background:var(--field);border:1px solid #aab;font:18px "Josefin Sans",sans-serif;color:#333;padding:7px 8px;margin-bottom:12px}
.field.area{height:216px}
.send{margin-top:40px;width:110px;height:36px;background:var(--btn);color:#fff;border:0;font:600 20px "Josefin Sans",sans-serif}
/* footer */
.footer{left:0;top:2636px;width:1200px;height:100px;background:linear-gradient(180deg,#b8e07a,var(--grass))}
.follow{left:40px;top:2662px;font-family:"Pinyon Script",cursive;font-size:34px;color:#fff}
.social{top:2660px;width:52px;height:52px;border-radius:50%;background:var(--btn)}
.copy{right:40px;top:2696px;font-size:14px;color:#234}
.to-top{right:30px;top:2560px;font-size:16px;text-align:center;color:var(--muted)}
</style>
</head>
<body>
<span class="abs page-tag">Built page</span>
<nav class="abs site-nav">
  <a href="#" class="active" style="left:30px">Home</a>
  <a href="#" style="left:180px">About</a>
  <a href="#" style="left:310px">Gallery</a>
  <span class="nav-brand">Brightcomb</span>
  <a href="#" style="left:650px">Services</a>
  <a href="#" style="left:810px">Contact</a>
</nav>

<div class="abs hero" role="img" aria-label="Slider photo of a woman with glossy auburn hair and a man with styled dark hair"></div>
<span class="abs hero-arrow" style="left:50px"></span>
<span class="abs hero-arrow" style="left:1114px"></span>

<header class="abs brand">
  <div class="brand-name">Brightcomb</div>
  <div class="brand-sub">Hair &amp; Makeup</div>
</header>

<h2 class="abs section-head" style="top:980px">Services</h2>
<div class="abs service" style="left:60px"><div class="photo" role="img" aria-label="Stylist cutting a client's hair" style="background:linear-gradient(#c9b7a0,#eee)"></div><p>Hair Cut</p></div>
<div class="abs service" style="left:340px"><div class="photo" role="img" aria-label="Woman with bright red coloured hair" style="background:linear-gradient(#d2572a,#f0d8c4)"></div><p>Hair Color</p></div>
<div class="abs service" style="left:620px"><div class="photo" role="img" aria-label="Man in a suit with a sharp hairstyle" style="background:linear-gradient(#3c3c3c,#d9d9d9)"></div><p>Hair Style</p></div>
<div class="abs service" style="left:900px"><div class="photo" role="img" aria-label="Woman with finished makeup and curled hair" style="background:linear-gradient(#c88a5a,#f2e2d2)"></div><p>Make up</p></div>

<h2 class="abs section-head" style="top:1376px">Works</h2>
<div class="abs works">
  <div role="img" aria-label="Portfolio: blonde woman in yellow" style="background:linear-gradient(#c9a46a,#7a8a3a)"></div>
  <div role="img" aria-label="Portfolio: bridal updo" style="background:linear-gradient(#e8e0d4,#b7a898)"></div>
  <div role="img" aria-label="Portfolio: men's styled cut" style="background:linear-gradient(#5a4a40,#d8cfc6)"></div>
  <div role="img" aria-label="Portfolio: brunette bob" style="background:linear-gradient(#6a4a3a,#cfc3b8)"></div>
  <div role="img" aria-label="Portfolio: man in dark shirt" style="background:linear-gradient(#2f2f2f,#9a9a9a)"></div>
</div>
<span class="abs hero-arrow" style="left:22px;top:1534px"></span>
<span class="abs hero-arrow" style="left:1142px;top:1534px"></span>

<div class="abs timeline">
  <div class="years">
    <span style="left:10px">1986</span><span style="left:190px">2007</span><span style="left:370px">2008</span><span style="left:540px">2009</span><span style="left:720px">20011</span><span style="left:900px">20013</span><span style="left:1020px">20014</span>
  </div>
  <svg width="1080" height="70" viewBox="0 0 1080 70" aria-hidden="true">
    <line x1="0" y1="10" x2="1080" y2="10" stroke="#555" stroke-width="2"/>
    <g stroke="#777" stroke-width="1.5">
      <path d="M0 10v20M30 10v10M60 10v10M90 10v14M120 10v10M150 10v10M180 10v20M210 10v10M240 10v10M270 10v14M300 10v10M330 10v10M360 10v20M390 10v10M420 10v10M450 10v14M480 10v10M510 10v10M540 10v20M570 10v10M600 10v10M630 10v14M660 10v10M690 10v10M720 10v20M750 10v10M780 10v10M810 10v14M840 10v10M870 10v10M900 10v20M930 10v10M960 10v10M990 10v14M1020 10v10M1050 10v10M1080 10v20"/>
    </g>
    <rect x="0" y="40" width="180" height="8" fill="#e04a7a"/>
    <rect x="180" y="40" width="180" height="8" fill="#8cc63f"/>
    <rect x="360" y="40" width="180" height="8" fill="#29a9e0"/>
    <rect x="540" y="40" width="180" height="8" fill="#f7931e"/>
    <rect x="720" y="40" width="180" height="8" fill="#ed1c24"/>
    <rect x="900" y="40" width="180" height="8" fill="#7e57c2"/>
    <g fill="#1d4f74"><circle cx="10" cy="44" r="8"/><circle cx="220" cy="44" r="8"/><circle cx="400" cy="44" r="8"/><circle cx="560" cy="44" r="8"/><circle cx="740" cy="44" r="8"/><circle cx="920" cy="44" r="8"/><circle cx="1060" cy="44" r="8"/></g>
  </svg>
  <div class="events">
    <span style="left:0;top:40px">Birth</span>
    <span style="left:150px;top:40px">Lorem ipsum is a dummy</span>
    <span style="left:280px;top:0">Lorem ipsum is a dummy</span>
    <span style="left:410px;top:80px">Lorem ipsum is a dummy</span>
    <span style="left:540px;top:10px">Lorem ipsum</span>
    <span style="left:665px;top:10px">Lorem ipsum is a dummy</span>
    <span style="left:790px;top:10px">Lorem ipsum is a dummy</span>
    <span style="left:900px;top:80px">Lorem ipsum is a dummy</span>
  </div>
</div>

<h2 class="abs section-head" style="top:2036px">Contact</h2>
<p class="abs contact-lead">Everything Begins with the Hello</p>
<div class="abs person" role="img" aria-label="Illustrated woman holding a question mark sign"></div>
<p class="abs contact-intro">Have a question, desire more information, or just want to have a chat?</p>
<p class="abs contact-line" style="top:2370px"><svg width="40" height="40" viewBox="0 0 24 24" aria-hidden="true"><path fill="#d9342b" d="M6.6 10.8a15 15 0 0 0 6.6 6.6l2.2-2.2c.3-.3.7-.4 1-.2 1.1.4 2.3.6 3.6.6.6 0 1 .4 1 1V20c0 .6-.4 1-1 1A17 17 0 0 1 3 4c0-.6.4-1 1-1h3.5c.6 0 1 .4 1 1 0 1.3.2 2.5.6 3.6.1.3 0 .7-.2 1z"/></svg>843 555 0142</p>
<p class="abs contact-line small" style="top:2454px"><svg width="40" height="28" viewBox="0 0 40 28" aria-hidden="true"><rect x="1" y="1" width="38" height="26" rx="3" fill="#f7a823"/><path d="M2 3l18 13L38 3" stroke="#fff" stroke-width="2" fill="none"/></svg>hello@brightcombstudio-example.com</p>
<p class="abs thanks">We look forward to hearing from you</p>

<p class="abs form-title">Write a message here</p>
<form class="abs contact-form">
  <input class="field" type="text" placeholder="Your Name">
  <input class="field" type="email" placeholder="Your E-mail">
  <textarea class="field area" placeholder="Your Message"></textarea>
  <button class="send" type="submit">Send</button>
</form>
<p class="abs to-top">Back to<br>Top</p>

<footer class="abs footer"></footer>
<p class="abs follow">Follow me on</p>
<span class="abs social" style="left:280px" aria-label="Social profile one"></span>
<span class="abs social" style="left:364px" aria-label="Social profile two"></span>
<span class="abs social" style="left:448px" aria-label="Social profile three"></span>
<p class="abs copy">© 2013 Brightcomb. All Rights Reserved</p>
</body>
</html>
```